Wealth Education Business Needs Sharp Business Card Design

We need a business card design for a recently launched investor education business called Harbor Crest.

The final design should promote security, empowerment, self improvement and financial gain. The card will ideally promote the stature of the business.

For more information and colours please visit harborcrest.com.au

Target Market(s)

Corporate executives and high net worth individuals

Industry/Entity Type

Education

Contact Information for Business Card

```html
<!DOCTYPE html>
<html lang="en">
<head>
<meta charset="utf-8">
<title>Harbor Crest – Business Card</title>
<link rel="stylesheet" href="https://fonts.googleapis.com/css2?family=Lato:wght@400;700&display=swap">
<style>
  :root {
    --stage-center: #e8eefb;
    --stage-edge: #c8d7f1;
    --card-white: #ffffff;
    --ink: #1f1f1f;
    --wordmark: #3a3535;
    --teal: #0e6b63;
    --icon: #135f5a;
    --mark-dot: #1d8a86;
    --tint-blue: rgba(205, 225, 245, 0.75);
    --tint-grey: rgba(208, 220, 222, 0.8);
    --tint-green: rgba(226, 236, 212, 0.8);
  }
  * { margin: 0; padding: 0; box-sizing: border-box; }
  html, body { width: 1200px; height: 965px; overflow: hidden; }
  body {
    position: relative;
    font-family: "Lato", Arial, sans-serif;
    color: var(--ink);
    background: radial-gradient(ellipse at 50% 50%, var(--stage-center) 0%, var(--stage-edge) 100%);
  }
  .card {
    position: absolute;
    left: 285px;
    width: 630px;
    height: 360px;
    background: var(--card-white);
    border-radius: 22px;
    box-shadow: 0 3px 8px rgba(40, 60, 100, 0.28);
    overflow: hidden;
  }
  .card--front { top: 80px; }
  .card--back { top: 525px; }

  /* soft tinted field standing in for the bar pattern */
  .pattern-field { position: absolute; }
  .card--front .pattern-field {
    left: 190px; top: 60px; width: 440px; height: 300px;
    background:
      linear-gradient(180deg, rgba(255,255,255,0.85) 0%, rgba(255,255,255,0) 45%),
      linear-gradient(90deg, rgba(255,255,255,0) 0%, var(--tint-grey) 35%, var(--tint-grey) 65%, var(--tint-green) 100%);
  }
  .card--back .pattern-field {
    inset: 0;
    background:
      linear-gradient(180deg, rgba(255,255,255,0.7) 0%, rgba(255,255,255,0) 40%),
      linear-gradient(90deg, var(--tint-blue) 0%, var(--tint-grey) 45%, var(--tint-grey) 70%, var(--tint-green) 100%);
  }

  .wordmark {
    position: absolute;
    display: flex;
    align-items: center;
    color: var(--wordmark);
    font-weight: 400;
    text-transform: uppercase;
    white-space: nowrap;
  }
  .wordmark__dot { border-radius: 50%; background: var(--mark-dot); flex: none; }
  .card--front .wordmark {
    left: 28px; top: 48px; height: 54px;
    font-size: 30px; letter-spacing: 4px; gap: 16px;
  }
  .card--front .wordmark__dot { width: 40px; height: 40px; }
  .card--back .wordmark {
    left: 0; right: 0; top: 140px; height: 90px;
    justify-content: center;
    font-size: 56px; letter-spacing: 4px; gap: 22px;
  }
  .card--back .wordmark__dot { width: 64px; height: 64px; }

  .person {
    position: absolute;
    right: 39px; top: 43px;
    text-align: right;
  }
  .person__name { font-size: 25px; font-weight: 700; color: var(--teal); line-height: 1.1; }
  .person__role { font-size: 17px; font-weight: 700; line-height: 1.3; }

  .contact-list {
    position: absolute;
    left: 27px; top: 152px;
    list-style: none;
    font-size: 17px;
    line-height: 21.5px;
  }
  .contact-list li { display: flex; align-items: center; gap: 6px; }
  .contact-list svg { width: 16px; height: 16px; fill: var(--icon); flex: none; }

  .address {
    position: absolute;
    left: 27px; top: 284px;
    display: flex; gap: 6px;
    font-size: 17px; line-height: 21.5px;
    font-style: normal;
  }
  .address svg { width: 16px; height: 16px; fill: var(--icon); margin-top: 2px; flex: none; }
</style>
</head>
<body>

<section class="card card--front" aria-label="Business card front">
  <div class="pattern-field" role="img" aria-label="Faint vertical bar pattern in pale grey and green"></div>

  <div class="wordmark"><span>Harbor</span><span class="wordmark__dot"></span><span>Crest</span></div>

  <div class="person">
    <div class="person__name">Daniel Hart</div>
    <div class="person__role">Director</div>
  </div>

  <ul class="contact-list">
    <li>
      <svg viewBox="0 0 16 16" aria-hidden="true"><path d="M1 5c0-2 3-3 7-3s7 1 7 3v1h-4V5H5v1H1z"/><path d="M4 7h8l2 6H2z"/></svg>
      <span>1300 555 014</span>
    </li>
    <li>
      <svg viewBox="0 0 16 16" aria-hidden="true"><path d="M4 0h8a1 1 0 0 1 1 1v14a1 1 0 0 1-1 1H4a1 1 0 0 1-1-1V1a1 1 0 0 1 1-1zm1 2v10h6V2zm3 11a1 1 0 1 0 0 2 1 1 0 0 0 0-2z"/></svg>
      <span>+613 5550 1234</span>
    </li>
    <li>
      <svg viewBox="0 0 16 16" aria-hidden="true"><path d="M0 3h16v10H0zm1.5 1.2v.4L8 9l6.5-4.4v-.4zM1.5 6v5.8h13V6L8 10.4z"/></svg>
      <span>support@harborcrest.com.au</span>
    </li>
    <li>
      <svg viewBox="0 0 16 16" aria-hidden="true"><path d="M8 0a8 8 0 1 0 0 16A8 8 0 0 0 8 0zm5.9 7.2h-2.4a12 12 0 0 0-1-4.6 6.5 6.5 0 0 1 3.4 4.6zM8 1.6c.8 1 1.4 3 1.5 5.6h-3C6.6 4.6 7.2 2.6 8 1.6zM5.5 2.6a12 12 0 0 0-1 4.6H2.1a6.5 6.5 0 0 1 3.4-4.6zM2.1 8.8h2.4a12 12 0 0 0 1 4.6 6.5 6.5 0 0 1-3.4-4.6zM8 14.4c-.8-1-1.4-3-1.5-5.6h3c-.1 2.6-.7 4.6-1.5 5.6zm2.5-1a12 12 0 0 0 1-4.6h2.4a6.5 6.5 0 0 1-3.4 4.6z"/></svg>
      <span>www.harborcrest.com.au</span>
    </li>
  </ul>

  <address class="address">
    <svg viewBox="0 0 16 16" aria-hidden="true"><path d="M8 1 0 8h2v7h4.5v-4.5h3V15H14V8h2z"/></svg>
    <span>Level 2, 45 Wattle Street,<br>Eastbrook VIC 3999</span>
  </address>
</section>

<section class="card card--back" aria-label="Business card back">
  <div class="pattern-field" role="img" aria-label="Faint vertical bar pattern in pale blue, grey and green"></div>
  <div class="wordmark"><span>Harbor</span><span class="wordmark__dot"></span><span>Crest</span></div>
</section>

</body>
</html>
```